Homemaking training schools needs a Business Card design

Designer, Hello!

No special requirements, good-looking enough.
--------------------------------------------------------------------------

Name: Marcus Dole
Chairman
Tel: 0574-71948263
Mobile: 13857420916
Email: kelvora@mailnest.example
Web: www.prt2019.example
Add: No.258, LanpingJie, BeiyuanQu, Ningbo, Zhejiang

LOGO
Ningbo PRT Homemaking Training School

Target Market(s)

pregnant women, mothers, infants, the elderly and families, including cleaning, cooking, nursing training.

Industry/Entity Type

Business

Contact Information for Business Card

Name: Marcus Dole
Chairman
Tel: 0574-71948263
Mobile: 13857420916
Email: kelvora@mailnest.example
Web: www.prt2019.example

LOGO

Font styles to use
Serif
Sans Serif
Decorative

Requirements
Nice to have
• Feels: clean, specifications, safety, comfort, warmth and happiness.

```html
<!DOCTYPE html>
<html lang="en">
<head>
<meta charset="utf-8">
<title>PinRuiTang Business Card</title>
<link rel="stylesheet" href="https://fonts.googleapis.com/css2?family=Raleway:wght@400;500;700&display=swap">
<style>
  :root {
    --brand-blue: #0a72c0;
    --brand-pink: #e5097f;
    --paper: #ffffff;
    --backdrop: #b6e0d7;
    --type-light: #ffffff;
  }
  * { box-sizing: border-box; margin: 0; padding: 0; }
  html, body {
    width: 1200px; height: 856px; overflow: hidden;
    background: var(--backdrop);
    font-family: "Raleway", sans-serif;
  }
  .sheet {
    position: relative; width: 1200px; height: 856px;
    display: flex; flex-direction: column; align-items: center; justify-content: center; gap: 56px;
  }
  .card {
    position: relative; width: 560px; height: 336px;
    background: var(--paper); border-radius: 26px; overflow: hidden;
    box-shadow: 0 10px 28px rgba(40, 90, 80, 0.18);
  }
  .card-art { position: absolute; inset: 0; width: 100%; height: 100%; }
  .brand {
    position: absolute; display: flex; align-items: center; gap: 8px;
    color: var(--brand-blue); font-weight: 700; font-size: 28px; letter-spacing: 0.5px;
    white-space: nowrap;
  }
  .brand-dot { width: 14px; height: 14px; border-radius: 50%; background: var(--brand-pink); }
  .card-back .brand { left: 50%; top: 50%; transform: translate(-50%, -50%); }
  .card-front .brand { right: 40px; top: 46px; font-size: 26px; }
  .holder { position: absolute; left: 40px; top: 108px; color: var(--brand-blue); }
  .holder-name { font-size: 27px; font-weight: 500; letter-spacing: 1px; text-transform: uppercase; line-height: 1.1; }
  .holder-role { font-size: 19px; font-weight: 500; margin-top: 2px; padding-left: 10px; }
  .contact-list {
    position: absolute; right: 290px; top: 214px; list-style: none;
    color: var(--type-light); font-size: 15px; line-height: 25px; text-align: right;
  }
  .contact-list li { display: flex; align-items: center; justify-content: flex-end; gap: 10px; white-space: nowrap; }
  .contact-icon { width: 15px; height: 15px; flex: none; }
  .divider { position: absolute; left: 290px; top: 210px; width: 1px; height: 96px; background: var(--type-light); }
  .address {
    position: absolute; left: 308px; top: 200px; font-style: normal;
    color: var(--type-light); font-size: 15px; line-height: 22px;
  }
</style>
</head>
<body>
<main class="sheet">

  <section class="card card-back" aria-label="Card back">
    <svg class="card-art" viewBox="0 0 560 336" aria-hidden="true">
      <path d="M0 336 L0 250 C 120 300, 260 318, 380 336 Z" fill="var(--brand-blue)"/>
      <path d="M0 244 C 120 292, 260 312, 380 330" fill="none" stroke="var(--brand-pink)" stroke-width="5"/>
      <path d="M560 0 L560 96 C 440 46, 300 22, 180 0 Z" fill="var(--brand-blue)"/>
      <path d="M560 102 C 440 52, 300 28, 180 6" fill="none" stroke="var(--brand-pink)" stroke-width="5"/>
    </svg>
    <div class="brand"><span class="brand-dot"></span>PinRuiTang</div>
  </section>

  <section class="card card-front" aria-label="Card front">
    <svg class="card-art" viewBox="0 0 560 336" aria-hidden="true">
      <path d="M0 226 C 150 188, 320 168, 560 118 L560 336 L0 336 Z" fill="var(--brand-blue)"/>
    </svg>
    <div class="brand"><span class="brand-dot"></span>PinRuiTang</div>
    <div class="holder">
      <h1 class="holder-name">Marcus Dole</h1>
      <p class="holder-role">Chairman</p>
    </div>
    <ul class="contact-list">
      <li>0574-71948263
        <svg class="contact-icon" viewBox="0 0 16 16" fill="none" stroke="#fff" stroke-width="1.3"><circle cx="8" cy="8" r="7"/><path d="M5.5 4.5l1.5 0 .6 2-1 .8a5 5 0 0 0 2.1 2.1l.8-1 2 .6v1.5a1 1 0 0 1-1 1A6 6 0 0 1 4.5 5.5a1 1 0 0 1 1-1z"/></svg></li>
      <li>13857420916
        <svg class="contact-icon" viewBox="0 0 16 16" fill="none" stroke="#fff" stroke-width="1.3"><circle cx="8" cy="8" r="7"/><rect x="5.7" y="4" width="4.6" height="8" rx="1"/></svg></li>
      <li>kelvora@mailnest.example
        <svg class="contact-icon" viewBox="0 0 16 16" fill="none" stroke="#fff" stroke-width="1.3"><rect x="1.5" y="3.5" width="13" height="9"/><path d="M1.5 3.5l6.5 5 6.5-5"/></svg></li>
      <li>www.prt2019.example
        <svg class="contact-icon" viewBox="0 0 16 16" fill="none" stroke="#fff" stroke-width="1.3"><circle cx="8" cy="8" r="7"/><ellipse cx="8" cy="8" rx="3" ry="7"/><path d="M1 8h14"/></svg></li>
    </ul>
    <div class="divider"></div>
    <address class="address">No.258, LanpingJie,<br>BeiyuanQu, Ningbo<br>Zhejiang</address>
  </section>

</main>
</body>
</html>
```